Quorva - corporate Business Card

We need a good look and innovative business card for a new start up company based in Los Angeles called "Quorva". We are in a payment business, including payment card, app, and ewallet. We are expert in online payment and Card not present (CNP) transaction.
We need an innovative, modern business card.

Our logo font is Aero Matics

Target Market(s)

Startup - Bank - Online Payment - Card Manufacturing

Industry/Entity Type

Startup

Contact Information for Business Card

phone: 555 014 7396 - Address: 4172 Marlowe blvd, Brenmoor City, CA 90299

Requirements
Must have
• Message: innovative, professional, expert, high tech, trust, online payment expert, security
Nice to have
• no comment
Should not have
• no Comment

```html
<!DOCTYPE html>
<html lang="en">
<head>
<meta charset="utf-8">
<title>Quorva – Business Card</title>
<link rel="stylesheet" href="https://fonts.googleapis.com/css2?family=Exo+2:wght@700&family=Open+Sans:wght@400;600&display=swap">
<style>
  :root {
    --brand-red: #c0202e;
    --card-dark: #2e2e30;
    --card-white: #ffffff;
    --ink: #4a4a4a;
    --ink-light: #d6d6d6;
    --stage: #d9d9dc;
  }
  * { margin: 0; padding: 0; box-sizing: border-box; }
  html, body { width: 1200px; height: 1000px; overflow: hidden; }
  body {
    background: var(--stage);
    font-family: "Open Sans", Arial, sans-serif;
    position: relative;
  }
  .card {
    position: absolute;
    left: 215px;
    width: 770px;
    height: 440px;
    border-radius: 24px;
    overflow: hidden;
  }
  .card-back { top: 40px; background: var(--card-dark); }
  .card-front { top: 520px; background: var(--card-white); }

  .back-pattern { position: absolute; inset: 0; background: var(--card-dark); }

  .brand {
    position: absolute;
    display: flex;
    align-items: center;
    gap: 14px;
    color: var(--brand-red);
    font-family: "Open Sans", Arial, sans-serif;
    font-weight: 600;
    letter-spacing: 1px;
  }
  .brand-dot { border-radius: 50%; background: var(--brand-red); flex: none; }
  .card-back .brand { left: 0; right: 0; top: 140px; justify-content: center; font-size: 64px; }
  .card-back .brand-dot { width: 92px; height: 92px; }
  .back-web {
    position: absolute; left: 0; right: 0; top: 290px;
    text-align: center; color: var(--ink-light);
    font-size: 20px; letter-spacing: 4px;
  }

  .card-front .brand { right: 50px; top: 42px; font-size: 52px; }
  .card-front .brand-dot { width: 78px; height: 78px; }

  .holder-name {
    position: absolute; left: 78px; top: 128px;
    font-family: "Exo 2", Arial, sans-serif; font-weight: 700;
    font-size: 36px; color: var(--brand-red); letter-spacing: 1.5px;
  }
  .holder-role {
    position: absolute; left: 78px; top: 170px;
    font-size: 23px; color: var(--ink);
  }
  .divider { position: absolute; left: 74px; right: 0; top: 206px; height: 3px; background: var(--brand-red); }

  .contact-list { position: absolute; left: 84px; top: 232px; list-style: none; }
  .contact-list li {
    display: flex; align-items: center; gap: 16px;
    font-size: 20px; color: var(--ink); height: 34px;
  }
  .contact-list svg { width: 16px; height: 16px; fill: var(--brand-red); flex: none; }
  .accent { color: var(--brand-red); }

  .address {
    position: absolute; right: 78px; top: 300px;
    text-align: right; font-size: 20px; line-height: 27px; color: var(--ink);
  }
  .address-pin { position: absolute; right: 44px; top: 300px; width: 20px; height: 26px; fill: var(--brand-red); }

  .footer-band { position: absolute; left: 0; bottom: 0; width: 770px; height: 60px; }
</style>
</head>
<body>

<section class="card card-back">
  <div class="back-pattern" role="img" aria-label="Faint repeating brand pattern across the dark card back"></div>
  <div class="brand"><span class="brand-dot"></span><span class="brand-name">quorva</span></div>
  <p class="back-web">www.websitename.com</p>
</section>

<section class="card card-front">
  <div class="brand"><span class="brand-dot"></span><span class="brand-name">quorva</span></div>

  <h1 class="holder-name">DARIA KELLAN</h1>
  <p class="holder-role">Ceo &amp; Founder</p>
  <div class="divider"></div>

  <ul class="contact-list">
    <li>
      <svg viewBox="0 0 16 16"><path d="M3.5 1l2.6 3.2-1.4 1.7c.9 2 2.6 3.7 4.7 4.7l1.7-1.4L14.3 11.8 12.9 14.6C7 14.4 1.6 9 1.4 3.1z"/></svg>
      555 014 7396
    </li>
    <li>
      <svg viewBox="0 0 16 16"><path d="M1 3h14v1.2L8 9 1 4.2z M1 5.8l7 4.8 7-4.8V13H1z"/></svg>
      yourname@email.com
    </li>
    <li>
      <svg viewBox="0 0 16 16"><circle cx="8" cy="8" r="7"/><path d="M1 8h14M8 1v14M3 4h10M3 12h10" stroke="#fff" stroke-width="1" fill="none"/></svg>
      <span>www.<span class="accent">websitename</span>.com</span>
    </li>
  </ul>

  <p class="address">4172 Marlowe blvd<br>Brenmoor City, CA 90299</p>
  <svg class="address-pin" viewBox="0 0 20 26"><path d="M10 0C4.5 0 0 4.3 0 9.6 0 16.8 10 26 10 26s10-9.2 10-16.4C20 4.3 15.5 0 10 0zm0 13.5a4 4 0 110-8 4 4 0 010 8z"/></svg>

  <svg class="footer-band" viewBox="0 0 770 60" preserveAspectRatio="none">
    <path d="M0 48 H400 L425 22 H770 V60 H0 Z" fill="var(--brand-red)"/>
  </svg>
</section>

</body>
</html>
```